Design letter head and business card

Hello,

you should design a business card and letter paper for Kranichflug Marketing. In German we write this word with K insteat of C.

Company does not have a logo. But in general, we write Kranichflug Marketing in 2 lines.
First line red: KRANICHFLUG
Second line gray: MARKETING

Red (or wine red) and Gray / Black are our favorite colors.

Company slogan: "Fresh Ground Online Marketing".

Company offers SEO, SEM, SEA, AdWords, Conversion Optimization, Online Markting Consulting ...

The website is old, please do not use this as base for your task.

German letter paper sizes:
Viawable Dimensions : 210 x 297 mm
Needed file dimensions: 212 x 299 mm

Informations to include:

Address:
Kranichflug Marketing GmbH
Lindenweg 23
71592 Weinstadt
Germany

Geschäftsführer | CEO: Bernhard Olzner

Phone: +49 (0) 7151 846 27 05

Fax: +49 (0) 7151 846 27 88

Mail: info@kranichflug-beispiel.de

Web: www.kranichflug-beispiel.de

Amtsgericht Suttgart, HRB 537264

Bank: Rosenauer Bank
IBAN: DE827315480900XXXXXXXX
BIC: GENODES1RSQ

Thanks

Bernhard

Target Market(s)

People who likes to win the online marketing game.

Industry/Entity Type

Business

Contact Information for Business Card

Here is the personal text on the card:

Name:
Bernhard Olzner

Title:
Geschäftsführer | CEO

Address:
Kranichflug Marketing GmbH
Lindenweg 23
71592 Weinstadt
Germany

Phone:
+49 (0) 7151 846 27 05

Fax:
+49 (0) 7151 846 27 88

Mail:
olzner@kranichflug-beispiel.de

Web:
www.kranichflug-beispiel.de

Business Card:
Viewable Dimensions: 85 x 55 mm
Needed file dimensions: 87 x 57mm

Font styles to use
Sans Serif

Requirements
Nice to have
• It would be great to see the dynamics of a helicopter.

```html
<!DOCTYPE html>
<html lang="de">
<head>
<meta charset="utf-8">
<title>Kranichflug Marketing – Visitenkarte</title>
<link rel="stylesheet" href="https://fonts.googleapis.com/css2?family=Dosis:wght@500;800&family=Roboto+Condensed:wght@700&display=swap">
<style>
  :root {
    --wine: #8e1f22;
    --card: #e6e6e8;
    --ink: #2e2e30;
    --ink-soft: #3a3a3c;
  }
  * { margin: 0; padding: 0; box-sizing: border-box; }
  html, body { width: 668px; height: 1200px; overflow: hidden; background: var(--card); }
  .card {
    position: relative;
    width: 668px;
    height: 1200px;
    background: var(--card);
    font-family: "Dosis", sans-serif;
    font-weight: 500;
    color: var(--ink-soft);
    text-align: center;
  }
  .top-band {
    position: absolute; top: 0; left: 0;
    width: 100%; height: 52px;
    background: var(--wine);
  }
  .brand {
    position: absolute; top: 128px; left: 0; width: 100%;
  }
  .brand-dot {
    display: block; width: 26px; height: 26px; margin: 0 auto 24px;
    border-radius: 50%; background: var(--wine);
  }
  .brand-name {
    font-weight: 800;
    color: var(--wine);
    font-size: 40px;
    line-height: 38px;
    letter-spacing: 1px;
  }
  .brand-slogan {
    margin-top: 14px;
    font-size: 21px;
    color: var(--ink);
  }
  .person {
    position: absolute; top: 592px; left: 0; width: 100%;
  }
  .person-name {
    font-family: "Roboto Condensed", sans-serif;
    font-weight: 700;
    font-size: 48px;
    color: var(--wine);
    line-height: 62px;
  }
  .person-title {
    font-size: 31px;
    line-height: 40px;
    margin-top: 6px;
  }
  .address {
    position: absolute; top: 832px; left: 0; width: 100%;
    font-size: 35px; line-height: 47px; font-style: normal;
  }
  .contact {
    position: absolute; top: 998px; left: 0; width: 100%;
    font-size: 35px; line-height: 47px;
  }
</style>
</head>
<body>
  <main class="card">
    <div class="top-band"></div>

    <header class="brand">
      <span class="brand-dot"></span>
      <div class="brand-name">KRANICHFLUG<br>MARKETING</div>
      <div class="brand-slogan">Fresh Ground Online Marketing</div>
    </header>

    <section class="person">
      <h1 class="person-name">Bernhard Olzner</h1>
      <p class="person-title">Geschäftsführer | CEO</p>
    </section>

    <address class="address">
      Kranichflug Marketing GmbH,<br>
      Lindenweg 23,<br>
      71592 Weinstadt, Germany
    </address>

    <section class="contact">
      <p>Phone: +49 (0) 7151 846 27 05</p>
      <p>Fax: +49 (0) 7151 846 27 88</p>
      <p>E-mail: info@kranichflug-beispiel.de</p>
    </section>
  </main>
</body>
</html>
```